Hvac and insulation company needs good looking business card design

We are hvac and insulation company and looking for a new business cards that look to today standards designs

Target Market(s)

homeowners

Industry/Entity Type

Hvac

Contact Information for Business Card

Name: Walter Brinoku
Home comfort consultant
address: 4827 Dunmore St #215 Oakland, CA 94619
office: 888-316-2790
cell: 510-742-3185
Lic.# 584261
Email: walter@corvane-hvac.com
Web: corvane-hvac.com

Requirements
Must have
• clean and sleek look
Nice to have
• simple with a clean look
Should not have
• to busy business card

```html
<!DOCTYPE html>
<html lang="en">
<head>
<meta charset="utf-8">
<title>Corvane Home Solutions – Business Card</title>
<link rel="stylesheet" href="https://fonts.googleapis.com/css2?family=Oswald:wght@500&family=Work+Sans:wght@400;500;600&display=swap">
<style>
  :root {
    --backdrop: #262626;
    --card: #1b1b1b;
    --card-edge: #2a2a2a;
    --ink: #f2f2f2;
    --ink-soft: #bdbdbd;
    --accent: #f07f14;
  }
  * { box-sizing: border-box; margin: 0; padding: 0; }
  html, body {
    width: 1200px; height: 900px; overflow: hidden;
    background: var(--backdrop);
    font-family: "Work Sans", sans-serif;
    color: var(--ink);
  }
  .canvas {
    width: 1200px; height: 900px;
    display: flex; flex-direction: column; align-items: center; justify-content: center;
    gap: 40px;
  }
  .card {
    position: relative;
    width: 700px; height: 400px;
    background: var(--card);
    border: 1px solid var(--card-edge);
    box-shadow: 0 12px 30px rgba(0,0,0,.45);
  }

  /* Front */
  .brand {
    position: absolute; left: 0; right: 0; top: 120px;
    display: flex; align-items: center; justify-content: center; gap: 22px;
  }
  .brand-square { width: 70px; height: 70px; background: #111; border: 1px solid #333; }
  .brand-text { display: flex; flex-direction: column; }
  .brand-name {
    font-size: 74px; font-weight: 500; letter-spacing: 2px; line-height: 1;
    color: var(--ink-soft);
  }
  .brand-tagline {
    font-size: 20px; font-weight: 500; letter-spacing: 5px; line-height: 1.2;
    color: var(--ink-soft);
  }
  .license {
    position: absolute; left: 0; right: 0; bottom: 44px;
    text-align: center; font-size: 20px; letter-spacing: 1px;
  }

  /* Back */
  .identity {
    position: absolute; left: 90px; top: 132px; width: 270px;
  }
  .person-name {
    font-family: "Oswald", sans-serif; font-weight: 500;
    font-size: 40px; line-height: 1; color: var(--accent); text-transform: uppercase;
    letter-spacing: -0.5px;
  }
  .person-role { font-size: 19px; letter-spacing: 1px; margin-top: 6px; }
  .divider {
    position: absolute; left: 385px; top: 130px;
    width: 3px; height: 90px; background: var(--accent);
  }
  .contacts {
    position: absolute; left: 410px; top: 136px;
    list-style: none; font-size: 18px; letter-spacing: 0.6px; line-height: 1.3;
  }
  .contacts li { display: flex; align-items: center; gap: 10px; }
  .contacts svg { width: 12px; height: 12px; flex: none; }
  .contacts .highlight { color: var(--accent); }
  .address {
    position: absolute; left: 90px; bottom: 60px;
    display: flex; align-items: center; gap: 14px;
    font-size: 20px; letter-spacing: 1px;
  }
  .address-square { width: 24px; height: 24px; background: var(--accent); }
</style>
</head>
<body>
<main class="canvas">
  <section class="card card-front">
    <div class="brand">
      <span class="brand-square"></span>
      <div class="brand-text">
        <span class="brand-name">corvane</span>
        <span class="brand-tagline">home solutions</span>
      </div>
    </div>
    <p class="license">Lic.# 584261</p>
  </section>

  <section class="card card-back">
    <div class="identity">
      <h1 class="person-name">Walter Brinoku</h1>
      <p class="person-role">Home comfort consultant</p>
    </div>
    <span class="divider"></span>
    <ul class="contacts">
      <li>
        <svg viewBox="0 0 12 12" fill="none" stroke="var(--accent)" stroke-width="1.5"><path d="M2.5 1.5l2 2-1 1.2c.6 1.4 1.7 2.5 3 3l1.2-1 2 2-1.2 1.3C5 9.8 2.2 7 1.3 2.7z"/></svg>
        888-316-2790
      </li>
      <li>
        <svg viewBox="0 0 12 12" fill="none" stroke="var(--accent)" stroke-width="1.5"><rect x="3" y="1" width="6" height="10" rx="1"/><path d="M5.5 9h1"/></svg>
        510-742-3185
      </li>
      <li>
        <svg viewBox="0 0 12 12" fill="none" stroke="var(--accent)" stroke-width="1.3"><rect x="1" y="2.5" width="10" height="7"/><path d="M1 2.5l5 4 5-4"/></svg>
        walter@corvane-hvac.com
      </li>
      <li>
        <svg viewBox="0 0 12 12" fill="none" stroke="var(--accent)" stroke-width="1.2"><circle cx="6" cy="6" r="5"/><ellipse cx="6" cy="6" rx="2.2" ry="5"/><path d="M1 6h10"/></svg>
        <span>www.<span class="highlight">corvane-hvac</span>.com</span>
      </li>
    </ul>
    <p class="address"><span class="address-square"></span>4827 Dunmore St #215 Oakland, CA 94619</p>
  </section>
</main>
</body>
</html>
```